Recruitment Agency in Texas, needs a stand out header letter

Our colours are red and grey and can be found on our website
just my logo will be sufficient and address...

Target Market(s)

Engineering Manufacturing

Colors
0094D4
00A9DD
6FCCEA
C7EBF8
E9F6FB
EB3D1F
EC4F4E
F09395
F8D3D4
FCEDEE

Requirements
Must have
• use colors red and grey
Should not have
• Please use same colors and font as my logo. My website is keltrayrecruitment.com

```html
<!DOCTYPE html>
<html lang="en">
<head>
<meta charset="utf-8">
<title>Keltray Recruitment Letterhead</title>
<link rel="stylesheet" href="https://fonts.googleapis.com/css2?family=Roboto:wght@300;400;500&family=Great+Vibes&display=swap">
<style>
  :root {
    --backdrop: #e4e4e4;
    --paper: #f3f3f3;
    --ink: #2a2a2a;
    --grey: #646569;
    --red: #e01f26;
    --band-1: #88141a;
    --band-2: #bf2127;
    --band-3: #de3a22;
    --band-4: #e6714c;
    --band-5: #ea9572;
  }
  * { box-sizing: border-box; margin: 0; padding: 0; }
  html, body {
    width: 1200px; height: 1200px; overflow: hidden;
    background: var(--backdrop);
  }
  .letterhead {
    position: absolute; left: 203px; top: 40px;
    width: 794px; height: 1120px;
    background: var(--paper);
    box-shadow: 0 2px 10px rgba(0,0,0,0.12);
    font-family: "Roboto", "Helvetica Neue", Arial, sans-serif;
    font-weight: 300;
    color: var(--ink);
  }
  .brand {
    position: absolute; left: 58px; top: 64px;
    display: flex; align-items: center; gap: 10px;
  }
  .brand-mark {
    width: 14px; height: 14px;
    background: var(--red);
  }
  .brand-name {
    font-family: "Roboto", "Helvetica Neue", Arial, sans-serif;
    font-weight: 500; font-size: 30px; line-height: 34px;
    letter-spacing: -0.3px;
    color: var(--grey);
  }
  .office-address {
    position: absolute; left: 557px; top: 57px;
    padding-left: 12px;
    border-left: 2px solid var(--red);
    font-style: normal;
    font-size: 13.3px; line-height: 16px;
    color: var(--grey); font-weight: 300;
  }
  .letter-body {
    position: absolute; left: 85px; top: 267px; width: 624px;
    font-size: 13.2px; line-height: 18.6px;
  }
  .letter-body p { text-align: justify; margin-bottom: 18.6px; }
  .letter-body .letter-date { margin-bottom: 18.6px; }
  .letter-body .recipient { margin-bottom: 36px; text-align: left; }
  .letter-body .greeting { margin-bottom: 18px; }
  .closing { margin-top: 57px; }
  .signature {
    font-family: "Great Vibes", cursive;
    font-size: 32px; line-height: 40px; margin-left: 4px;
  }
  .colour-band {
    position: absolute; left: 0; bottom: 0; width: 100%; height: 17px;
    display: flex;
  }
  .colour-band span { flex: 1; }
  .colour-band span:nth-child(1) { background: var(--band-1); }
  .colour-band span:nth-child(2) { background: var(--band-2); }
  .colour-band span:nth-child(3) { background: var(--band-3); }
  .colour-band span:nth-child(4) { background: var(--band-4); }
  .colour-band span:nth-child(5) { background: var(--band-5); }
</style>
</head>
<body>
<main class="letterhead">
  <header>
    <div class="brand">
      <span class="brand-mark" aria-hidden="true"></span>
      <span class="brand-name">Keltray Recruitment</span>
    </div>
    <address class="office-address">
      Central Houston Office<br>
      48 Brazos Park Suite 900<br>
      Houston, TX 77019
    </address>
  </header>

  <section class="letter-body">
    <p class="letter-date">01 January 2050</p>
    <p class="recipient">Company (Pvt) Ltd.<br>PO Box 3355 Mainville St<br>Sample City Country 3355</p>
    <p class="greeting">Dear Daniel Hartwell,</p>
    <p>Lorem ipsum dolor sit amet, consectetuer adipiscing elit, sed diam nonummy nibh euismod tincidunt ut laoreet dolore magna aliquam erat volutpat. Ut wisi enim ad minim veniam, quis nostrud exerci tation ullamcorper suscipit lobortis nisl ut aliquip ex ea commodo consequat. Duis dolore te feugait nulla facilisi. Nam liber tempor cum soluta nobis eleifend option congue nihil imperdiet doming id quod mazim placerat facer possim assum. Lorem ipsum dolor sit amet, consectetuer adipiscing elit, sed diam nonummy nibh euismod tincidunt ut laoreet dolore magna aliquam erat volutpat. Ut wisi enim ad minim veniam, quis nostrud exerci tation ullamcorper suscipit lobortis nisl ut aliquip ex ea commodo consequat.</p>
    <p>Consectetuer adipiscing elit, sed diam nonummy nibh euismod tincidunt ut laoreet dolore magna aliquam erat volutpat. Ut wisi enim ad minim veniam, quis nostrud exerci tation ullamcorper suscipit lobortis nisl ut aliquip ex ea commodo consequat. Consectetuer adipiscing elit, sed diam nonummy nibh euismod tincidunt ut laoreet dolore magna aliquam erat volutpat. Ut wisi enim ad minim veniam, quis nostrud exerci tation ullamcorper suscipit lobortis nisl ut aliquip ex ea commodo consequat.</p>
    <p>Consectetuer adipiscing elit, sed diam nonummy nibh euismod tincidunt ut laoreet dolore magna aliquam erat volutpat. Ut wisi enim ad minim veniam, quis nostrud exerci tation ullamcorper suscipit lobortis nisl ut aliquip ex ea commodo consequat. Consectetuer adipiscing elit, sed diam nonummy nibh euismod tincidunt ut laoreet dolore magna aliquam erat volutpat. Ut wisi enim ad minim veniam, quis nostrud exerci tation ullamcorper suscipit lobortis nisl ut aliquip ex ea commodo consequat.</p>
    <div class="closing">Sincerely Yours</div>
    <div class="signature">Owen Calder</div>
  </section>

  <footer class="colour-band" aria-hidden="true">
    <span></span><span></span><span></span><span></span><span></span>
  </footer>
</main>
</body>
</html>
```